Meridale Bed Company Needs Business Card

Looking for a very nice looking business card. Creative but not extravagant. We sell beds and pillows across the U.S. and need something professional but catchy. I have attached the logo.

Name : Devin Holt
Title : President
Phone : (800) 471-2960
Email: sleep@quilmora.com
Website: www.quilmora.com

Can be single-sided or double-sided
horizontal or vertical

Can use Blues/Greys

Target Market(s)

Mass Market

Industry/Entity Type

Retail

Contact Information for Business Card

Name : Devin Holt
Title : President
Phone : (800) 471-2960
Email: sleep@quilmora.com
Website: www.quilmora.com

Requirements
Must have
• Clean, Modern, Smooth
• Can use Blues/Greys
• On the other side without the information - have something simple like www.quilmora.com or our logo
Nice to have
• Surprise me
Should not have
• Nothing crazy, nothing cluttered

```html
<!DOCTYPE html>
<html lang="en">
<head>
<meta charset="utf-8">
<title>Meridale Bed Company – Business Card</title>
<link rel="stylesheet" href="https://fonts.googleapis.com/css2?family=Open+Sans:wght@300;400;600;700&display=swap">
<style>
  :root {
    --sky: #34a3d6;
    --paper: #ffffff;
    --ink: #2b2b2b;
    --backdrop: #eceff1;
    --edge: #d5dadd;
  }
  * { margin: 0; padding: 0; box-sizing: border-box; }
  html, body {
    width: 1200px; height: 900px; overflow: hidden;
    background: var(--backdrop);
    font-family: "Open Sans", Arial, sans-serif;
  }
  .sheet {
    width: 1200px; height: 900px;
    display: flex; align-items: center; justify-content: center; gap: 40px;
  }
  .card {
    position: relative;
    width: 560px; height: 320px;
    box-shadow: 0 6px 18px rgba(0,0,0,0.12);
    overflow: hidden;
  }
  .card--front { background: var(--paper); border: 1px solid var(--edge); }
  .card--back { background: var(--sky); color: var(--paper); }

  .wordmark {
    position: absolute; left: 0; right: 0;
    text-align: center;
    font-weight: 300;
    letter-spacing: 3px;
    line-height: 1;
  }
  .card--front .wordmark { top: 92px; font-size: 74px; color: var(--sky); }
  .card--back .wordmark { top: 62px; font-size: 70px; color: var(--paper); }

  .web-rule {
    position: absolute; left: 0; right: 0; top: 206px;
    display: flex; align-items: center; gap: 10px;
  }
  .web-rule .rule { flex: 1; height: 2px; background: var(--sky); }
  .web-rule .web {
    font-size: 13px; font-weight: 700; letter-spacing: 1.2px; color: var(--ink);
  }

  .divider {
    position: absolute; left: 0; right: 0; top: 168px;
    height: 2px; background: var(--paper);
  }
  .contact {
    position: absolute; right: 22px; top: 186px;
    list-style: none; text-align: right;
    font-size: 12.5px; line-height: 21px;
  }
  .contact li { display: flex; justify-content: flex-end; align-items: center; gap: 6px; }
  .contact svg { width: 11px; height: 11px; fill: var(--paper); }
  .person { position: absolute; left: 24px; bottom: 34px; }
  .person .name { font-size: 22px; font-weight: 700; line-height: 1.1; }
  .person .title { font-size: 15px; font-weight: 400; padding-left: 14px; }
</style>
</head>
<body>
<main class="sheet">
  <section class="card card--front" aria-label="Card front">
    <div class="wordmark">quilmora</div>
    <div class="web-rule">
      <span class="rule"></span>
      <span class="web">www.quilmora.com</span>
      <span class="rule"></span>
    </div>
  </section>

  <section class="card card--back" aria-label="Card back">
    <div class="wordmark">quilmora</div>
    <div class="divider"></div>
    <ul class="contact">
      <li>(800) 471-2960
        <svg viewBox="0 0 12 12" aria-hidden="true"><path d="M1 4c0-2 2-3 5-3s5 1 5 3v1H8.5V4h-5v1H1zM3 6h6l1.5 5h-9z"/></svg>
      </li>
      <li>sleep@quilmora.com
        <svg viewBox="0 0 12 12" aria-hidden="true"><path d="M0 2h12v8H0zm1 1v.4l5 3.2 5-3.2V3z"/></svg>
      </li>
      <li>www.quilmora.com
        <svg viewBox="0 0 12 12" aria-hidden="true"><circle cx="6" cy="6" r="5.5"/></svg>
      </li>
    </ul>
    <div class="person">
      <div class="name">Devin Holt</div>
      <div class="title">President</div>
    </div>
  </section>
</main>
</body>
</html>
```